TeaLantern Flyer

I require an A5 sized flyer to be designed that advertised the new flexible workspace of TeaLantern.
should say it is a "Flexible Workspace with EV Charging"
web address is www.tealantern.co.uk
It should show the 3 different types of membership as priced on the website

```html
<!DOCTYPE html>
<html lang="en">
<head>
<meta charset="utf-8">
<title>TeaLantern Flyer</title>
<link rel="stylesheet" href="https://fonts.googleapis.com/css2?family=Exo+2:ital,wght@0,200;0,300;1,800;1,900&family=Oswald:wght@300;600&family=Poppins:wght@400;500&display=swap">
<style>
:root{
  --orange:#f08a0c;
  --ink:#1c1c1c;
  --charcoal:#3a3a3a;
  --blue:#3e6ee0;
  --card:#e6e7ea;
  --paper:#f5f5f6;
  --stage:#e9ebee;
  --text:#2c2c2c;
  --white:#ffffff;
}
*{box-sizing:border-box;margin:0;padding:0}
html,body{width:1200px;height:2185px;overflow:hidden;background:var(--stage)}
.flyer{position:absolute;left:0;top:240px;width:1200px;height:1704px;background:linear-gradient(180deg,var(--white),var(--paper));overflow:hidden;font-family:"Poppins",sans-serif;color:var(--text)}
.header-art{position:absolute;left:0;top:0;width:1200px;height:760px}
.brand{position:absolute;left:80px;top:90px;font-family:"Poppins",sans-serif;font-weight:500;font-size:72px;line-height:1;color:var(--ink);letter-spacing:-1px}
.headline{position:absolute;left:80px;top:222px;color:var(--white)}
.headline .light{display:block;font-family:"Exo 2",sans-serif;font-weight:200;font-size:72px;letter-spacing:4px;line-height:76px}
.headline .mid{display:block;font-family:"Oswald",sans-serif;font-weight:600;font-size:76px;line-height:80px;letter-spacing:-1px}
.headline .mid small{font-weight:300;font-size:52px}
.headline .accent{display:block;font-family:"Exo 2",sans-serif;font-style:italic;font-weight:900;font-size:84px;line-height:82px;color:var(--orange)}
.intro{position:absolute;left:80px;top:506px;width:500px;padding-left:24px;border-left:5px solid var(--orange);color:var(--white);font-size:23px;line-height:27.5px}
.plans{position:absolute;left:70px;top:750px;width:1071px;height:715px;display:flex}
.plan{position:relative;height:715px;background:var(--card);display:flex;flex-direction:column}
.plan--day{width:348px;border-radius:8px 0 0 8px}
.plan--light{width:365px;box-shadow:0 0 18px rgba(0,0,0,.18);z-index:2}
.plan--all{width:358px;border-radius:0 8px 8px 0}
.plan-head{position:relative;height:194px;clip-path:polygon(0 0,100% 0,100% 80%,50% 100%,0 80%)}
.plan--day .plan-head{background:var(--charcoal)}
.plan--light .plan-head{background:var(--orange)}
.plan--all .plan-head{background:var(--blue)}
.plan-icon{position:absolute;left:50%;top:-28px;transform:translateX(-50%);width:116px;height:116px;border-radius:50%;border:5px solid var(--white);display:flex;align-items:center;justify-content:center;z-index:3}
.plan--day .plan-icon{background:var(--blue);top:-14px;width:108px;height:108px}
.plan--light .plan-icon{background:var(--charcoal);top:-48px;width:130px;height:130px}
.plan--all .plan-icon{background:var(--charcoal);top:-30px}
.plan-title{position:absolute;left:0;right:0;top:104px;text-align:center;color:var(--white);font-family:"Exo 2",sans-serif;font-style:italic;font-weight:900;font-size:36px;line-height:31px}
.features{list-style:none;padding:0 20px 0 48px;flex:1}
.plan--day .features{margin-top:56px;padding-left:72px}
.plan--light .features{margin-top:42px;padding-left:40px}
.plan--all .features{margin-top:30px;padding-left:50px}
.features li{position:relative;font-size:19.5px;line-height:22px;margin-bottom:16px}
.features li::before{content:"";position:absolute;left:-26px;top:4px;width:15px;height:15px;border-radius:50%;background:var(--orange)}
.features li::after{content:"";position:absolute;left:-22px;top:8px;width:6px;height:3px;border-left:2px solid var(--white);border-bottom:2px solid var(--white);transform:rotate(-45deg)}
.price{height:110px;color:var(--white);text-align:center;display:flex;flex-direction:column;justify-content:center}
.plan--day .price{background:var(--charcoal);border-radius:0 0 0 12px}
.plan--light .price{background:var(--orange);border-radius:0 0 12px 12px;height:125px;margin-bottom:-15px}
.plan--all .price{background:var(--blue);border-radius:0 0 12px 0}
.amount{font-family:"Exo 2",sans-serif;font-style:italic;font-weight:900;font-size:50px;line-height:50px}
.plan--day .amount,.plan--all .amount{color:var(--orange)}
.amount small{font-family:"Poppins",sans-serif;font-style:normal;font-weight:400;font-size:21px;line-height:20px;display:inline-block;color:var(--white);text-align:left;vertical-align:middle}
.plan--light .amount{color:var(--ink);display:flex;justify-content:center;gap:22px}
.plan--light .sublabels{display:flex;justify-content:space-around;font-size:20px;line-height:20px;padding:0 34px}
.price-note{font-size:17.5px;margin-top:6px}
.ev-visual{position:absolute;left:66px;top:1454px;width:540px;height:250px;background:radial-gradient(ellipse at 55% 55%,#ffffff 0,#e4e6e9 55%,rgba(245,245,246,0) 75%)}
.contact{position:absolute;left:612px;top:1492px}
.contact h2{font-family:"Exo 2",sans-serif;font-style:italic;font-weight:900;font-size:50px;line-height:54px;color:var(--orange)}
.contact p{display:flex;align-items:center;gap:18px;font-size:28px;line-height:44px;color:var(--ink)}
.contact .dot{width:26px;height:26px;border-radius:50%;background:var(--orange);display:inline-flex;align-items:center;justify-content:center}
</style>
</head>
<body>
<main class="flyer">
  <svg class="header-art" viewBox="0 0 1200 760">
    <defs>
      <linearGradient id="lounge" x1="0" y1="0" x2="1" y2="1">
        <stop offset="0" stop-color="#d9dcdf"/>
        <stop offset=".45" stop-color="#8a837c"/>
        <stop offset=".75" stop-color="#6b4a33"/>
        <stop offset="1" stop-color="#a27b52"/>
      </linearGradient>
    </defs>
    <rect x="0" y="192" width="680" height="8" fill="var(--orange)"/>
    <polygon points="0,200 1200,200 1200,660 1160,740 700,740 650,660 0,660" fill="var(--ink)"/>
    <polygon points="0,660 650,660 700,740 1160,740 1200,660 1200,684 1170,752 690,752 640,678 0,678" fill="var(--orange)"/>
    <polygon points="586,376 736,79 1173,79 1290,376 1173,666 736,666" fill="#cfd2d5"/>
    <polygon role="img" aria-label="Photo of the lounge area with leather sofas, coffee tables and hot desks" points="598,376 744,92 1166,92 1276,376 1166,653 744,653" fill="url(#lounge)"/>
  </svg>

  <div class="brand">TeaLantern</div>

  <h1 class="headline">
    <span class="light">FLEXIBLE</span>
    <span class="mid">WORKSPACE <small>WITH</small></span>
    <span class="accent">EV Charging</span>
  </h1>

  <p class="intro">TeaLantern is a unique workspace environment for EV owners looking to recharge their Electric Vehicles, grab a snack and beverage, and catch up with some office work.</p>

  <section class="plans">
    <article class="plan plan--day">
      <div class="plan-head">
        <h3 class="plan-title">Day<br>Member</h3>
      </div>
      <div class="plan-icon">
        <svg width="50" height="44" viewBox="0 0 50 44" fill="none" stroke="#fff" stroke-width="3"><rect x="3" y="11" width="44" height="30" rx="4"/><path d="M17 11V5h16v6M3 22h44M22 22v5h6v-5"/></svg>
      </div>
      <ul class="features">
        <li>Use of Hot Desks &amp; Lounge Areas</li>
        <li>Secure Wifi</li>
        <li>Free Tea &amp; Coffee</li>
      </ul>
      <div class="price">
        <div class="amount">£25.00 <small>Each<br>visit</small></div>
        <div class="price-note">Price Inclusive of VAT Each Visit</div>
      </div>
    </article>

    <article class="plan plan--light">
      <div class="plan-head">
        <h3 class="plan-title">Light<br>Member</h3>
      </div>
      <div class="plan-icon">
        <svg width="66" height="66" viewBox="0 0 66 66" fill="none" stroke="#fff" stroke-width="3.5"><circle cx="30" cy="36" r="24"/><circle cx="30" cy="36" r="15"/><circle cx="30" cy="36" r="6"/><path d="M30 36L56 10M50 6v10h10"/></svg>
      </div>
      <ul class="features">
        <li>Use of Hot Desks &amp; Lounge Areas</li>
        <li>Secure Wifi</li>
        <li>Free Tea &amp; Coffee</li>
        <li>Discounted E/V Charge Rates</li>
        <li>Access to Meeting Rooms (£10+vat per person, per hour)</li>
      </ul>
      <div class="price">
        <div class="amount"><span>£18</span><span>+</span><span>£18</span></div>
        <div class="sublabels"><span>a month</span><span>Each Visit</span></div>
        <div class="price-note">Price Inclusive of VAT &nbsp;Per month</div>
      </div>
    </article>

    <article class="plan plan--all">
      <div class="plan-head">
        <h3 class="plan-title">All Access<br>Member</h3>
      </div>
      <div class="plan-icon">
        <svg width="58" height="50" viewBox="0 0 58 50" fill="none" stroke="var(--orange)" stroke-width="3" stroke-linejoin="round"><path d="M14 3h30l12 14-27 30L2 17z M2 17h54 M14 3l8 14 7-14 7 14 8-14 M22 17l7 30 7-30"/></svg>
      </div>
      <ul class="features">
        <li>Unlimited Number of Visits Each Month</li>
        <li>Dedicated Desk (lockable draws+£60 a month)</li>
        <li>Receptionist to Meet &amp; Greet Guests</li>
        <li>Use of Lounge Areas</li>
        <li>Secure Wifi</li>
        <li>Free Tea &amp; Coffee</li>
        <li>Discounted E/V Charge Rates</li>
        <li>Access to Meeting Rooms (£10+vat per person/ hr)</li>
      </ul>
      <div class="price">
        <div class="amount">£180.00</div>
        <div class="price-note">Price Inclusive of VAT &nbsp;Per month</div>
      </div>
    </article>
  </section>

  <div class="ev-visual" role="img" aria-label="White electric car parked beside a charging station"></div>

  <section class="contact">
    <h2>Contact us</h2>
    <p><span class="dot"><svg width="14" height="10" viewBox="0 0 14 10" fill="none" stroke="#fff" stroke-width="1.6"><rect x="1" y="1" width="12" height="8"/><path d="M1 1l6 5 6-5"/></svg></span>info@tealantern.co.uk</p>
    <p><span class="dot"><svg width="16" height="16" viewBox="0 0 16 16" fill="none" stroke="#fff" stroke-width="1.4"><circle cx="8" cy="8" r="6.5"/><path d="M1.5 8h13M8 1.5c-3 3.5-3 9.5 0 13M8 1.5c3 3.5 3 9.5 0 13"/></svg></span>www.tealantern.co.uk</p>
  </section>
</main>
</body>
</html>
```